Build PowerPoint for New Logo & Letterhead

I have started my own consulting firm and created a logo and letterhead (attached) am looking PowerPoint template. My name is Dorrit Vandermolen and the company is called K Quadrant Advisory. We primarily use PowerPoint files to display analyses, maps and key talking points from interviews and/or recommendations. We use the documents more to facilitate discussion with our target audiences. Most of the time our PowerPoint document is printed as handouts for our clients and not projected.

Target Market(s)

Healthcare provider organizations (hospitals, health systems, physician groups)

Industry/Entity Type

Healthcare

Font styles to use
Sans Serif

Colors
abd036
1f9ad1
0355a3

Requirements
Must have
• I would like to cover page to play off of the letterhead in some fashion. I want the design to provide plenty of space for text, graphics, maps, pictures, etc.
• We will usually include our clients logo somewhere on the document. Historically it is prominent on the cover page and then in one of the corners on all of the pages thereafter.

```html
<!DOCTYPE html>
<html lang="en">
<head>
<meta charset="utf-8">
<title>K Quadrant Advisory – Presentation Template</title>
<link href="https://fonts.googleapis.com/css2?family=Open+Sans:wght@400;600;700&display=swap" rel="stylesheet">
<style>
:root{
  --green:#abd036;
  --sky:#1f9ad1;
  --navy:#0355a3;
  --ink:#333;
  --body:#5a5a5a;
  --paper:#fff;
  --bg:#e9e9ea;
  --pale:#eef6fb;
  --gray:#9a9a9a;
}
*{box-sizing:border-box;margin:0;padding:0}
html,body{width:905px;height:1200px;overflow:hidden}
body{background:var(--bg);font-family:"Open Sans",Arial,sans-serif;color:var(--ink)}
.deck{display:grid;grid-template-columns:repeat(3,285px);grid-auto-rows:161px;column-gap:10px;row-gap:7px;padding:17px 15px}
.slide{position:relative;background:var(--paper);overflow:hidden;box-shadow:0 1px 2px rgba(0,0,0,.12)}
.abs{position:absolute}
.title{position:absolute;left:15px;top:13px;font-size:11px;font-weight:600;color:var(--ink)}
.sub{font-size:5px;font-weight:700;color:var(--sky);margin-bottom:2px}
.txt{font-size:4.3px;line-height:1.4;color:var(--body)}
.txt ul{list-style:none}
.txt li{position:relative;padding-left:5px;margin-bottom:1px}
.txt li:before{content:"•";position:absolute;left:0;color:var(--navy)}
.txt li.sub2{padding-left:11px}
.txt li.sub2:before{content:"–";left:6px}
.mark{display:inline-flex;align-items:center;gap:3px;font-size:5px;font-weight:700;color:var(--navy);letter-spacing:.3px}
.mark i{display:inline-block;width:7px;height:7px;background:var(--navy)}
.mark.light{color:#fff}.mark.light i{background:#fff}
.foot{position:absolute;left:0;bottom:0;width:285px;height:14px}
.foot .mark{position:absolute;left:13px;bottom:2px;font-size:3.5px}
.foot .mark i{width:5px;height:5px}
.foot .copy{position:absolute;left:120px;bottom:3px;font-size:2.6px;color:var(--gray)}
.foot .pg{position:absolute;right:10px;bottom:3px;font-size:2.6px;color:var(--gray)}
.photo{position:absolute}
.label{font-size:4.5px;font-weight:700;color:#fff}
</style>
</head>
<body>
<main class="deck">

<!-- 1 cover with photo -->
<section class="slide" style="background:var(--sky)">
  <div class="photo" role="img" aria-label="Blue-tinted photo of business people walking" style="inset:0;background:linear-gradient(180deg,#2aa3dc 0%,#1b8cc6 60%,#2f9fd6 100%)"></div>
  <p class="abs txt" style="left:40px;right:40px;top:58px;text-align:center;color:#fff;font-size:5.5px"><b>Lorem ipsum</b> dolor sit amet, consectetur adipiscing elit. Suspendisse eget ligula mollis, mattis libero eget, rutrum ipsum.</p>
  <p class="abs txt" style="left:0;right:0;top:80px;text-align:center;color:#dff1fa;font-size:3.2px">Copyright © 2016 K Quadrant Advisory All rights reserved.</p>
  <div class="abs" style="left:0;right:0;top:102px;text-align:center"><span class="mark light" style="font-size:6px"><i></i>K QUADRANT ADVISORY</span></div>
</section>

<!-- 2 title slide -->
<section class="slide">
  <svg class="abs" width="285" height="161" viewBox="0 0 285 161">
    <rect width="285" height="161" fill="var(--pale)"/>
    <polygon points="0,0 285,0 285,105 160,105 145,118 0,118" fill="var(--sky)"/>
    <polygon points="145,118 160,105 285,105 285,110 163,110 150,121 0,121 0,118" fill="var(--navy)"/>
    <polygon points="0,158 285,158 285,161 0,161" fill="var(--sky)"/>
  </svg>
  <div class="abs" style="left:8px;top:127px;font-size:11px;font-weight:700;color:var(--sky)">Presentation Title</div>
  <div class="abs" style="left:8px;top:142px;font-size:6px;color:var(--ink)">Subheading Presentation Title</div>
  <div class="abs" style="left:8px;top:154px;font-size:3.5px;color:var(--body)">May 2016</div>
  <div class="abs" style="right:10px;top:134px"><span class="mark" style="font-size:4px"><i></i>K QUADRANT ADVISORY</span></div>
</section>

<!-- 3 title slide variant -->
<section class="slide">
  <svg class="abs" width="285" height="161" viewBox="0 0 285 161">
    <rect width="285" height="161" fill="var(--pale)"/>
    <polygon points="0,0 285,0 285,114 0,114" fill="var(--sky)"/>
    <polygon points="0,114 160,114 172,122 285,122 285,126 170,126 158,118 0,118" fill="var(--navy)"/>
    <rect y="157" width="285" height="4" fill="var(--sky)"/>
  </svg>
  <div class="abs" style="left:16px;top:44px;font-size:13px;font-weight:700;color:#fff">Presentation Title</div>
  <div class="abs" style="left:16px;top:62px;font-size:6.5px;color:#e4f4fb">Subheading Presentation Title</div>
  <div class="abs" style="left:16px;top:76px;font-size:3.8px;color:#e4f4fb">May 2016</div>
  <div class="abs" style="left:10px;top:131px"><span class="mark" style="font-size:4px"><i></i>K QUADRANT<br>ADVISORY</span></div>
  <div class="abs" style="left:58px;top:135px;font-size:3.6px;color:var(--navy);line-height:2.4">Email: dorrit@kquadrantadvisory.co<br>Telephone: 555.014.2087</div>
</section>

<!-- 4 section slide blue -->
<section class="slide">
  <svg class="abs" width="285" height="161" viewBox="0 0 285 161">
    <rect width="285" height="161" fill="var(--pale)"/>
    <polygon points="0,0 285,0 285,136 160,136 150,127 0,127" fill="var(--sky)"/>
    <polygon points="0,127 150,127 160,136 285,136 285,140 158,140 148,131 0,131" fill="var(--navy)"/>
    <rect y="157" width="285" height="4" fill="var(--sky)"/>
  </svg>
  <div class="abs" style="right:10px;top:104px"><span class="mark light" style="font-size:4px"><i></i>K QUADRANT ADVISORY</span></div>
  <div class="abs" style="left:8px;top:137px;font-size:8.5px;font-weight:700;color:var(--sky)">Section Slide</div>
  <div class="abs" style="left:8px;top:149px;font-size:5.5px;color:var(--ink)">Divider Presentation Title</div>
</section>

<!-- 5 section slide green -->
<section class="slide">
  <svg class="abs" width="285" height="161" viewBox="0 0 285 161">
    <rect width="285" height="161" fill="#f4f8ea"/>
    <polygon points="0,0 285,0 285,136 160,136 150,127 0,127" fill="var(--green)"/>
    <polygon points="0,127 150,127 160,136 285,136 285,140 158,140 148,131 0,131" fill="var(--sky)"/>
    <rect y="157" width="285" height="4" fill="var(--green)"/>
  </svg>
  <div class="abs" style="right:10px;top:104px"><span class="mark light" style="font-size:4px"><i></i>K QUADRANT ADVISORY</span></div>
  <div class="abs" style="left:8px;top:137px;font-size:8.5px;font-weight:700;color:var(--sky)">Section Slide</div>
  <div class="abs" style="left:8px;top:149px;font-size:5.5px;color:var(--ink)">Divider Presentation Title</div>
</section>

<!-- 6 table of content -->
<section class="slide">
  <h2 class="title">Table of Content</h2>
  <div class="abs" style="left:15px;top:36px;width:260px;display:grid;grid-template-columns:repeat(3,1fr);row-gap:10px;column-gap:12px">
    <div><div style="display:flex;align-items:center;gap:4px;font-size:4.8px;font-weight:600"><span style="width:14px;height:14px;border:1.2px solid var(--green);border-radius:50%;display:flex;align-items:center;justify-content:center;color:var(--navy);font-size:6px">1</span>Lorem Ipsum</div><p class="txt" style="margin-top:3px">Lorem ipsum dolor sit amet, te ullum corpora delicata duo. Rebum insolens pri eu. No alia tota modus qui.</p></div>
    <div><div style="display:flex;align-items:center;gap:4px;font-size:4.8px;font-weight:600"><span style="width:14px;height:14px;border:1.2px solid var(--green);border-radius:50%;display:flex;align-items:center;justify-content:center;color:var(--navy);font-size:6px">2</span>Lorem Ipsum</div><p class="txt" style="margin-top:3px">Lorem ipsum dolor sit amet, te ullum corpora delicata duo. Rebum insolens pri eu. No alia tota modus qui.</p></div>
    <div><div style="display:flex;align-items:center;gap:4px;font-size:4.8px;font-weight:600"><span style="width:14px;height:14px;border:1.2px solid var(--green);border-radius:50%;display:flex;align-items:center;justify-content:center;color:var(--navy);font-size:6px">3</span>Lorem Ipsum</div><p class="txt" style="margin-top:3px">Lorem ipsum dolor sit amet, te ullum corpora delicata duo. Rebum insolens pri eu. No alia tota modus qui.</p></div>
    <div><div style="display:flex;align-items:center;gap:4px;font-size:4.8px;font-weight:600"><span style="width:14px;height:14px;border:1.2px solid var(--green);border-radius:50%;display:flex;align-items:center;justify-content:center;color:var(--navy);font-size:6px">4</span>Lorem Ipsum</div><p class="txt" style="margin-top:3px">Lorem ipsum dolor sit amet, te ullum corpora delicata duo. Rebum insolens pri eu. No alia tota modus qui.</p></div>
    <div><div style="display:flex;align-items:center;gap:4px;font-size:4.8px;font-weight:600"><span style="width:14px;height:14px;border:1.2px solid var(--green);border-radius:50%;display:flex;align-items:center;justify-content:center;color:var(--navy);font-size:6px">5</span>Lorem Ipsum</div><p class="txt" style="margin-top:3px">Lorem ipsum dolor sit amet, te ullum corpora delicata duo. Rebum insolens pri eu. No alia tota modus qui.</p></div>
    <div><div style="display:flex;align-items:center;gap:4px;font-size:4.8px;font-weight:600"><span style="width:14px;height:14px;border:1.2px solid var(--green);border-radius:50%;display:flex;align-items:center;justify-content:center;color:var(--navy);font-size:6px">6</span>Lorem Ipsum</div><p class="txt" style="margin-top:3px">Lorem ipsum dolor sit amet, te ullum corpora delicata duo. Rebum insolens pri eu. No alia tota modus qui.</p></div>
  </div>
  <div class="foot"><svg width="285" height="14"><path d="M0 4H45L50 9H285" stroke="var(--green)" stroke-width="1" fill="none"/><path d="M0 12.5H285" stroke="var(--navy)" stroke-width="1"/></svg><span class="mark"><i></i>KQA</span><span class="copy">Copyright © 2016 K Quadrant Advisory All rights reserved.</span><span class="pg">6</span></div>
</section>

<!-- 7 one column -->
<section class="slide">
  <h2 class="title">One Column</h2>
  <div class="abs txt" style="left:15px;top:40px;width:255px">
    <p class="sub">Lorem Ipsum</p>
    <ul>
      <li>Lorem ipsum dolor sit amet, te ullum corpora delicata duo. Rebum insolens pri eu. No alia tota modus qui.</li>
      <li class="sub2">Sint brute at usu. Duo idque appareat adversarium at.</li>
      <li>Lorem ipsum dolor sit amet, te ullum corpora delicata duo. Rebum insolens pri eu. No alia tota modus qui.</li>
      <li class="sub2">Sint brute at usu. Duo idque appareat adversarium at.</li>
      <li>Lorem ipsum dolor sit amet, te ullum corpora delicata duo. Rebum insolens pri eu. No alia tota modus qui.</li>
      <li class="sub2">Sint brute at usu. Duo idque appareat adversarium at.</li>
      <li>Lorem ipsum dolor sit amet, te ullum corpora delicata duo. Rebum insolens pri eu. No alia tota modus qui.</li>
      <li class="sub2">Sint brute at usu. Duo idque appareat adversarium at.</li>
    </ul>
  </div>
  <div class="foot"><svg width="285" height="14"><path d="M0 4H45L50 9H285" stroke="var(--green)" stroke-width="1" fill="none"/><path d="M0 12.5H285" stroke="var(--navy)" stroke-width="1"/></svg><span class="mark"><i></i>KQA</span><span class="copy">Copyright © 2016 K Quadrant Advisory All rights reserved.</span><span class="pg">7</span></div>
</section>

<!-- 8 two column -->
<section class="slide">
  <h2 class="title">Two Column</h2>
  <div class="abs txt" style="left:15px;top:40px;width:120px">
    <p class="sub">Lorem Ipsum</p>
    <ul>
      <li>Lorem ipsum dolor sit amet, te ullum corpora delicata duo. Rebum insolens pri eu. No alia tota modus qui.</li>
      <li class="sub2">Sint brute at usu. Duo idque appareat adversarium at.</li>
      <li>Lorem ipsum dolor sit amet, te ullum corpora delicata duo. Rebum insolens pri eu. No alia tota modus qui.</li>
      <li class="sub2">Sint brute at usu. Duo idque appareat adversarium at.</li>
      <li>Lorem ipsum dolor sit amet, te ullum corpora delicata duo. Rebum insolens pri eu. No alia tota modus qui.</li>
    </ul>
  </div>
  <div class="abs" style="left:143px;top:40px;height:100px;border-left:.6px dashed #ccc"></div>
  <div class="abs txt" style="left:150px;top:40px;width:120px">
    <p class="sub">Lorem Ipsum</p>
    <ul>
      <li>Lorem ipsum dolor sit amet, te ullum corpora delicata duo. Rebum insolens pri eu. No alia tota modus qui.</li>
      <li class="sub2">Sint brute at usu. Duo idque appareat adversarium at.</li>
      <li>Lorem ipsum dolor sit amet, te ullum corpora delicata duo. Rebum insolens pri eu. No alia tota modus qui.</li>
      <li class="sub2">Sint brute at usu. Duo idque appareat adversarium at.</li>
      <li>Lorem ipsum dolor sit amet, te ullum corpora delicata duo. Rebum insolens pri eu. No alia tota modus qui.</li>
    </ul>
  </div>
  <div class="foot"><svg width="285" height="14"><path d="M0 4H45L50 9H285" stroke="var(--green)" stroke-width="1" fill="none"/><path d="M0 12.5H285" stroke="var(--navy)" stroke-width="1"/></svg><span class="mark"><i></i>KQA</span><span class="copy">Copyright © 2016 K Quadrant Advisory All rights reserved.</span><span class="pg">8</span></div>
</section>

<!-- 9 left column with pyramid -->
<section class="slide">
  <h2 class="title">Left Column</h2>
  <div class="abs txt" style="left:15px;top:40px;width:120px">
    <p class="sub">Lorem Ipsum</p>
    <ul>
      <li>Lorem ipsum dolor sit amet, te ullum corpora delicata duo. Rebum insolens pri eu. No alia tota modus qui.</li>
      <li class="sub2">Sint brute at usu. Duo idque appareat adversarium at.</li>
      <li>Lorem ipsum dolor sit amet, te ullum corpora delicata duo. Rebum insolens pri eu. No alia tota modus qui.</li>
      <li class="sub2">Sint brute at usu. Duo idque appareat adversarium at.</li>
      <li>Lorem ipsum dolor sit amet, te ullum corpora delicata duo. Rebum insolens pri eu. No alia tota modus qui.</li>
    </ul>
  </div>
  <div class="abs" style="left:143px;top:40px;height:100px;border-left:.6px dashed #ccc"></div>
  <svg class="abs" style="left:160px;top:40px" width="110" height="100" viewBox="0 0 110 100">
    <polygon points="55,0 67,19 43,19" fill="#cfd2d4"/>
    <polygon points="42,21 68,21 80,42 30,42" fill="var(--navy)"/>
    <polygon points="29,44 81,44 93,66 17,66" fill="var(--sky)"/>
    <polygon points="16,68 94,68 106,92 4,92" fill="var(--green)"/>
  </svg>
  <div class="foot"><svg width="285" height="14"><path d="M0 4H45L50 9H285" stroke="var(--green)" stroke-width="1" fill="none"/><path d="M0 12.5H285" stroke="var(--navy)" stroke-width="1"/></svg><span class="mark"><i></i>KQA</span><span class="copy">Copyright © 2016 K Quadrant Advisory All rights reserved.</span><span class="pg">9</span></div>
</section>

<!-- 10 right column with image -->
<section class="slide">
  <div class="photo" role="img" aria-label="Photo of a smiling doctor in a white coat with a stethoscope" style="left:0;top:0;width:138px;height:150px;background:linear-gradient(135deg,#f3f4f5 0%,#dfe3e6 55%,#c9ced3 100%)"></div>
  <h2 class="title" style="left:148px;top:17px;font-size:8.5px">Right Column With Image</h2>
  <div class="abs txt" style="left:150px;top:40px;width:122px">
    <p class="sub" style="color:var(--green)">Lorem Ipsum</p>
    <ul>
      <li>Lorem ipsum dolor sit amet, te ullum corpora delicata duo. Rebum insolens pri eu. No alia tota modus qui.</li>
      <li class="sub2">Sint brute at usu. Duo idque appareat adversarium at.</li>
      <li>Lorem ipsum dolor sit amet, te ullum corpora delicata duo. Rebum insolens pri eu. No alia tota modus qui.</li>
      <li class="sub2">Sint brute at usu. Duo idque appareat adversarium at.</li>
      <li>Lorem ipsum dolor sit amet, te ullum corpora delicata duo. Rebum insolens pri eu. No alia tota modus qui.</li>
    </ul>
  </div>
  <div class="foot"><svg width="285" height="14"><path d="M0 4H45L50 9H285" stroke="var(--green)" stroke-width="1" fill="none"/><path d="M0 12.5H285" stroke="var(--navy)" stroke-width="1"/></svg><span class="mark"><i></i>KQA</span><span class="copy">Copyright © 2016 K Quadrant Advisory All rights reserved.</span><span class="pg">10</span></div>
</section>

<!-- 11 our team -->
<section class="slide">
  <h2 class="title">Our Team</h2>
  <div class="abs" style="left:35px;top:36px;width:220px;display:grid;grid-template-columns:repeat(3,1fr);row-gap:6px;text-align:center">
    <div><div role="img" aria-label="Team member portrait" style="width:38px;height:38px;margin:0 auto;border-radius:50%;border:1.5px solid var(--green);background:radial-gradient(circle at 50% 40%,#e9ecee,#c6ccd1)"></div><div style="font-size:4.5px;font-weight:700;color:var(--sky);font-style:italic;margin-top:2px">John Doe</div><div style="font-size:3.5px;color:var(--gray)">Doctor</div></div>
    <div><div role="img" aria-label="Team member portrait" style="width:38px;height:38px;margin:0 auto;border-radius:50%;border:1.5px solid var(--green);background:radial-gradient(circle at 50% 40%,#e9ecee,#c6ccd1)"></div><div style="font-size:4.5px;font-weight:700;color:var(--sky);font-style:italic;margin-top:2px">John Doe</div><div style="font-size:3.5px;color:var(--gray)">Doctor</div></div>
    <div><div role="img" aria-label="Team member portrait" style="width:38px;height:38px;margin:0 auto;border-radius:50%;border:1.5px solid var(--green);background:radial-gradient(circle at 50% 40%,#e9ecee,#c6ccd1)"></div><div style="font-size:4.5px;font-weight:700;color:var(--sky);font-style:italic;margin-top:2px">John Doe</div><div style="font-size:3.5px;color:var(--gray)">Doctor</div></div>
    <div><div role="img" aria-label="Team member portrait" style="width:38px;height:38px;margin:0 auto;border-radius:50%;border:1.5px solid var(--green);background:radial-gradient(circle at 50% 40%,#e9ecee,#c6ccd1)"></div><div style="font-size:4.5px;font-weight:700;color:var(--sky);font-style:italic;margin-top:2px">John Doe</div><div style="font-size:3.5px;color:var(--gray)">Doctor</div></div>
    <div><div role="img" aria-label="Team member portrait" style="width:38px;height:38px;margin:0 auto;border-radius:50%;border:1.5px solid var(--green);background:radial-gradient(circle at 50% 40%,#e9ecee,#c6ccd1)"></div><div style="font-size:4.5px;font-weight:700;color:var(--sky);font-style:italic;margin-top:2px">John Doe</div><div style="font-size:3.5px;color:var(--gray)">Doctor</div></div>
    <div><div role="img" aria-label="Team member portrait" style="width:38px;height:38px;margin:0 auto;border-radius:50%;border:1.5px solid var(--green);background:radial-gradient(circle at 50% 40%,#e9ecee,#c6ccd1)"></div><div style="font-size:4.5px;font-weight:700;color:var(--sky);font-style:italic;margin-top:2px">John Doe</div><div style="font-size:3.5px;color:var(--gray)">Doctor</div></div>
  </div>
  <div class="foot"><svg width="285" height="14"><path d="M0 4H45L50 9H285" stroke="var(--green)" stroke-width="1" fill="none"/><path d="M0 12.5H285" stroke="var(--navy)" stroke-width="1"/></svg><span class="mark"><i></i>KQA</span><span class="copy">Copyright © 2016 K Quadrant Advisory All rights reserved.</span><span class="pg">11</span></div>
</section>

<!-- 12 table sample -->
<section class="slide">
  <h2 class="title">Table Sample</h2>
  <div class="abs" style="left:15px;top:37px;width:257px;display:grid;grid-template-columns:repeat(4,1fr);column-gap:1px;row-gap:1px;font-size:3.3px;color:var(--body)">
    <div style="background:var(--green);color:#fff;font-weight:700;font-size:4.2px;padding:4px 8px">Lorem ipsum</div>
    <div style="background:var(--sky);color:#fff;font-weight:700;font-size:4.2px;padding:4px 8px">Lorem ipsum 1</div>
    <div style="background:var(--navy);color:#fff;font-weight:700;font-size:4.2px;padding:4px 8px">Lorem ipsum 2</div>
    <div style="background:var(--gray);color:#fff;font-weight:700;font-size:4.2px;padding:4px 8px">Lorem ipsum 3</div>
    <div style="background:#eee;padding:3px;height:26px">• Lorem ipsum dolor sit amet, consectetur adipiscing elit.<br>• Quisque nec enim luctus.</div>
    <div style="background:#eee;padding:3px">• Lorem ipsum dolor sit amet, consectetur adipiscing elit.</div>
    <div style="background:#eee;padding:3px">• Lorem ipsum dolor sit amet, consectetur adipiscing elit.</div>
    <div style="background:#eee;padding:3px">• Lorem ipsum dolor sit amet, consectetur adipiscing elit.<br>• Quisque nec enim luctus.</div>
    <div style="background:#fff;padding:3px;height:30px">• Lorem ipsum dolor sit amet, consectetur adipiscing elit.</div>
    <div style="background:#fff;padding:3px">• Lorem ipsum dolor sit amet, consectetur adipiscing elit.</div>
    <div style="background:#fff;padding:3px">• Lorem ipsum dolor sit amet, consectetur adipiscing elit.<br>• Quisque nec enim luctus.</div>
    <div style="background:#fff;padding:3px">• Lorem ipsum dolor sit amet, consectetur adipiscing elit.<br>• Quisque nec enim luctus.</div>
    <div style="background:#eee;padding:3px;height:14px">• Lorem ipsum dolor sit amet.</div>
    <div style="background:#eee;padding:3px">• Lorem ipsum dolor sit amet.</div>
    <div style="background:#eee;padding:3px">• Lorem ipsum dolor sit amet.</div>
    <div style="background:#eee;padding:3px">• Lorem ipsum dolor sit amet.</div>
    <div style="background:#e2e2e2;padding:3px;height:14px">• Lorem ipsum dolor sit amet.</div>
    <div style="background:#e2e2e2;padding:3px">• Lorem ipsum dolor sit amet.</div>
    <div style="background:#e2e2e2;padding:3px">• Lorem ipsum dolor sit amet.</div>
    <div style="background:#e2e2e2;padding:3px">• Lorem ipsum dolor sit amet.</div>
  </div>
  <div class="foot"><svg width="285" height="14"><path d="M0 4H45L50 9H285" stroke="var(--green)" stroke-width="1" fill="none"/><path d="M0 12.5H285" stroke="var(--navy)" stroke-width="1"/></svg><span class="mark"><i></i>KQA</span><span class="copy">Copyright © 2016 K Quadrant Advisory All rights reserved.</span><span class="pg">12</span></div>
</section>

<!-- 13 about us -->
<section class="slide">
  <h2 class="title">About Us</h2>
  <div class="photo" role="img" aria-label="Circular photo of a smiling doctor" style="left:17px;top:40px;width:92px;height:92px;border-radius:50%;background:radial-gradient(circle at 50% 40%,#f1f3f4,#cdd2d6)"></div>
  <div class="abs txt" style="left:117px;top:40px;width:155px">
    <p class="sub">Lorem Ipsum is simply dummy</p>
    <p>Text of the printing and typesetting industry. Lorem Ipsum has been the industry's standard dummy text ever since the 1500s, when an unknown printer took a galley of type and scrambled it to make a type specimen book. It has survived not only five centuries, but also the leap into electronic typesetting, remaining essentially unchanged. It was popularised in the 1960s with the release of sheets containing Lorem Ipsum passages, and more recently with desktop publishing software including versions of Lorem Ipsum.</p>
    <p style="margin-top:2px">Lorem Ipsum has been the industry's standard dummy text ever since the 1500s, when an unknown printer took a galley of type and scrambled.</p>
  </div>
  <div class="foot"><svg width="285" height="14"><path d="M0 4H45L50 9H285" stroke="var(--green)" stroke-width="1" fill="none"/><path d="M0 12.5H285" stroke="var(--navy)" stroke-width="1"/></svg><span class="mark"><i></i>KQA</span><span class="copy">Copyright © 2016 K Quadrant Advisory All rights reserved.</span><span class="pg">13</span></div>
</section>

<!-- 14 pie chart -->
<section class="slide">
  <h2 class="title">Pie Chart Sample</h2>
  <div class="abs" style="left:0;right:0;top:42px;text-align:center;font-size:6px;font-weight:600">Lorem ipsum dolar sit amet</div>
  <svg class="abs" style="left:105px;top:54px" width="76" height="76" viewBox="0 0 42 42">
    <g transform="rotate(-90 21 21)">
      <circle cx="21" cy="21" r="10.5" fill="none" stroke="var(--green)" stroke-width="21" stroke-dasharray="33 66" />
      <circle cx="21" cy="21" r="10.5" fill="none" stroke="var(--sky)" stroke-width="21" stroke-dasharray="0 33 15.2 66" />
      <circle cx="21" cy="21" r="10.5" fill="none" stroke="var(--navy)" stroke-width="21" stroke-dasharray="0 48.2 6.6 66" />
      <circle cx="21" cy="21" r="10.5" fill="none" stroke="#e6e6e6" stroke-width="21" stroke-dasharray="0 54.8 11.2 66" />
    </g>
    <g fill="#fff" font-size="2.6" font-family="Open Sans, sans-serif"><text x="30" y="25">50%</text><text x="6.5" y="27">23%</text><text x="11" y="13">10%</text><text x="16.5" y="6.5" fill="#777">0%</text></g>
  </svg>
  <div class="abs" style="left:0;right:0;top:138px;display:flex;justify-content:center;gap:10px;font-size:3.2px;color:var(--body)">
    <span><b style="color:var(--green)">■</b> Lorem ipsum</span><span><b style="color:var(--sky)">■</b> Lorem ipsum</span><span><b style="color:var(--navy)">■</b> Lorem ipsum</span><span><b style="color:#ccc">■</b> Lorem ipsum</span>
  </div>
  <div class="foot"><svg width="285" height="14"><path d="M0 4H45L50 9H285" stroke="var(--green)" stroke-width="1" fill="none"/><path d="M0 12.5H285" stroke="var(--navy)" stroke-width="1"/></svg><span class="mark"><i></i>KQA</span><span class="copy">Copyright © 2016 K Quadrant Advisory All rights reserved.</span><span class="pg">14</span></div>
</section>

<!-- 15 chevron process -->
<section class="slide">
  <h2 class="title">Basic Chevron Process</h2>
  <svg class="abs" style="left:20px;top:38px" width="250" height="34" viewBox="0 0 250 34">
    <polygon points="0,0 82,0 92,17 82,34 0,34" fill="var(--green)"/>
    <polygon points="80,0 168,0 178,17 168,34 80,34 90,17" fill="var(--sky)"/>
    <polygon points="166,0 240,0 250,17 240,34 166,34 176,17" fill="var(--navy)"/>
    <g fill="#fff" font-size="6" font-family="Open Sans, sans-serif" text-anchor="middle"><text x="42" y="19">Lorem ipsum</text><text x="130" y="19">Lorem ipsum</text><text x="210" y="19">Lorem ipsum</text></g>
  </svg>
  <div class="abs" style="left:22px;top:80px;width:245px;display:grid;grid-template-columns:repeat(3,1fr);column-gap:12px">
    <ul class="txt" style="list-style:none"><li>Lorem ipsum dolor sit amet, consectetur adipiscing elit.</li><li>Nunc quis dui dolor</li><li>Maecenas sem nibh, congue a urna non, volutpat porttitor justo</li></ul>
    <ul class="txt" style="list-style:none"><li>Lorem ipsum dolor sit amet, consectetur adipiscing elit.</li><li>Nunc quis dui dolor</li><li>Maecenas sem nibh, congue a urna non, volutpat porttitor justo</li></ul>
    <ul class="txt" style="list-style:none"><li>Lorem ipsum dolor sit amet, consectetur adipiscing elit.</li><li>Nunc quis dui dolor</li><li>Maecenas sem nibh, congue a urna non, volutpat porttitor justo</li></ul>
  </div>
  <div class="foot"><svg width="285" height="14"><path d="M0 4H45L50 9H285" stroke="var(--green)" stroke-width="1" fill="none"/><path d="M0 12.5H285" stroke="var(--navy)" stroke-width="1"/></svg><span class="mark"><i></i>KQA</span><span class="copy">Copyright © 2016 K Quadrant Advisory All rights reserved.</span><span class="pg">15</span></div>
</section>

<!-- 16 linear venn -->
<section class="slide">
  <h2 class="title">Linier VEEN</h2>
  <svg class="abs" style="left:32px;top:45px" width="230" height="90" viewBox="0 0 230 90">
    <circle cx="45" cy="45" r="44" fill="var(--green)" opacity=".95"/>
    <circle cx="115" cy="45" r="44" fill="var(--sky)" opacity=".9"/>
    <circle cx="185" cy="45" r="44" fill="var(--navy)" opacity=".85"/>
  </svg>
  <p class="abs txt" style="left:47px;top:70px;width:60px;text-align:center;color:#fff">Lorem ipsum dolor sit amet, consectetur adipiscing elit. Nunc quis dui dolor. Maecenas sem nibh, congue a urna non, volutpat porttitor justo</p>
  <p class="abs txt" style="left:117px;top:70px;width:60px;text-align:center;color:#fff">Lorem ipsum dolor sit amet, consectetur adipiscing elit. Nunc quis dui dolor. Maecenas sem nibh, congue a urna non, volutpat porttitor justo</p>
  <p class="abs txt" style="left:187px;top:70px;width:60px;text-align:center;color:#fff">Lorem ipsum dolor sit amet, consectetur adipiscing elit. Nunc quis dui dolor. Maecenas sem nibh, congue a urna non, volutpat porttitor justo</p>
  <div class="foot"><svg width="285" height="14"><path d="M0 4H45L50 9H285" stroke="var(--green)" stroke-width="1" fill="none"/><path d="M0 12.5H285" stroke="var(--navy)" stroke-width="1"/></svg><span class="mark"><i></i>KQA</span><span class="copy">Copyright © 2016 K Quadrant Advisory All rights reserved.</span><span class="pg">16</span></div>
</section>

<!-- 17 bar chart -->
<section class="slide">
  <h2 class="title">Bar Chart Sample</h2>
  <div class="abs" style="left:0;right:0;top:42px;text-align:center;font-size:6px;font-weight:600">Lorem ipsum dolor sit amet</div>
  <svg class="abs" style="left:20px;top:52px" width="250" height="96" viewBox="0 0 250 96">
    <g stroke="#ddd" stroke-width=".4"><path d="M14 82H245"/></g>
    <g font-size="3.5" fill="#777" font-family="Open Sans, sans-serif" text-anchor="end"><text x="10" y="83">0</text><text x="10" y="70">1</text><text x="10" y="57">2</text><text x="10" y="44">3</text><text x="10" y="31">4</text><text x="10" y="18">5</text><text x="10" y="5">6</text></g>
    <rect x="24" y="30" width="8" height="52" fill="var(--green)"/>
    <rect x="47" y="51" width="8" height="31" fill="var(--green)"/>
    <rect x="70" y="40" width="8" height="42" fill="var(--green)"/>
    <rect x="93" y="26" width="8" height="56" fill="var(--sky)"/>
    <rect x="116" y="53" width="8" height="29" fill="var(--sky)"/>
    <rect x="139" y="67" width="8" height="15" fill="var(--sky)"/>
    <rect x="162" y="11" width="8" height="71" fill="var(--navy)"/>
    <rect x="185" y="47" width="8" height="35" fill="var(--navy)"/>
    <rect x="208" y="60" width="8" height="22" fill="var(--navy)"/>
    <rect x="231" y="38" width="8" height="44" fill="var(--gray)"/>
    <g font-size="3" fill="#777" font-family="Open Sans, sans-serif" text-anchor="middle"><text x="28" y="88">Category 1</text><text x="51" y="88">Category 2</text><text x="74" y="88">Category 3</text><text x="97" y="88">Category 4</text><text x="120" y="88">Category 5</text><text x="143" y="88">Category 6</text><text x="166" y="88">Category 7</text><text x="189" y="88">Category 8</text><text x="212" y="88">Category 9</text><text x="235" y="88">Category 10</text></g>
  </svg>
  <div class="foot"><svg width="285" height="14"><path d="M0 4H45L50 9H285" stroke="var(--green)" stroke-width="1" fill="none"/><path d="M0 12.5H285" stroke="var(--navy)" stroke-width="1"/></svg><span class="mark"><i></i>KQA</span><span class="copy">Copyright © 2016 K Quadrant Advisory All rights reserved.</span><span class="pg">17</span></div>
</section>

<!-- 18 graphic sample -->
<section class="slide">
  <h2 class="title">Graphic Sample</h2>
  <svg class="abs" style="left:108px;top:40px" width="70" height="100" viewBox="0 0 70 100">
    <circle cx="35" cy="50" r="28" fill="none" stroke="#cfd5d8" stroke-width="1.2"/>
    <g fill="#fff" stroke="var(--green)" stroke-width="1.2">
      <circle cx="35" cy="22" r="7"/><circle cx="59" cy="36" r="7"/><circle cx="59" cy="64" r="7"/><circle cx="35" cy="78" r="7"/><circle cx="11" cy="64" r="7"/><circle cx="11" cy="36" r="7"/>
    </g>
    <g fill="none" stroke="var(--navy)" stroke-width=".8">
      <rect x="32" y="19" width="6" height="6"/><circle cx="59" cy="36" r="2.6"/><path d="M56 66l6-4M56 62l6 4"/><rect x="33" y="74.5" width="4" height="7" rx=".6"/><circle cx="11" cy="64" r="3"/><rect x="8" y="33.5" width="6" height="4"/><path d="M10 39h2"/>
    </g>
  </svg>
  <div class="abs" style="left:118px;top:86px"><span class="mark" style="font-size:3.2px"><i style="width:5px;height:5px"></i>KQA</span></div>
  <p class="abs txt" style="left:115px;top:32px;width:60px;text-align:center">Lorem ipsum dolor sit amet, consectetur adipiscing elit</p>
  <p class="abs txt" style="left:40px;top:68px;width:64px;text-align:center">Lorem ipsum dolor sit amet, consectetur adipiscing elit</p>
  <p class="abs txt" style="left:40px;top:108px;width:64px;text-align:center">Lorem ipsum dolor sit amet, consectetur adipiscing elit</p>
  <p class="abs txt" style="left:182px;top:68px;width:70px;text-align:center">Lorem ipsum dolor sit amet, consectetur adipiscing elit</p>
  <p class="abs txt" style="left:182px;top:108px;width:70px;text-align:center">Lorem ipsum dolor sit amet, consectetur adipiscing elit</p>
  <p class="abs txt" style="left:115px;top:140px;width:60px;text-align:center">Lorem ipsum dolor sit amet</p>
  <div class="foot"><svg width="285" height="14"><path d="M0 4H45L50 9H285" stroke="var(--green)" stroke-width="1" fill="none"/><path d="M0 12.5H285" stroke="var(--navy)" stroke-width="1"/></svg><span class="mark"><i></i>KQA</span><span class="copy">Copyright © 2016 K Quadrant Advisory All rights reserved.</span><span class="pg">18</span></div>
</section>

<!-- 19 content with icons -->
<section class="slide">
  <div class="photo" role="img" aria-label="Faded photo of medical team in discussion" style="left:0;top:0;width:285px;height:100px;background:linear-gradient(90deg,#9aa7ae 0%,#c4ccd0 45%,#8d999f 100%)"></div>
  <h2 class="title" style="color:#fff;font-size:10px">Content With Icon Sample</h2>
  <div class="abs" style="left:0;top:100px;width:285px;height:61px;background:#fff"></div>
  <div class="abs" style="left:15px;top:84px;width:260px;display:grid;grid-template-columns:repeat(4,1fr);text-align:center">
    <div><svg width="26" height="26" viewBox="0 0 26 26"><circle cx="13" cy="13" r="12" fill="var(--green)" stroke="#fff" stroke-width="1.5"/><circle cx="12" cy="12" r="4" fill="none" stroke="#fff" stroke-width="1.4"/><path d="M15 15l4 4" stroke="#fff" stroke-width="1.6"/></svg><div style="font-size:5px;font-weight:700;color:var(--green)">Lorem Ipsum</div><p class="txt">Lorem ipsum dolor sit amet, consectetur adipiscing elit</p></div>
    <div><svg width="26" height="26" viewBox="0 0 26 26"><circle cx="13" cy="13" r="12" fill="var(--sky)" stroke="#fff" stroke-width="1.5"/><rect x="7" y="8" width="12" height="8" fill="none" stroke="#fff" stroke-width="1.3"/><path d="M11 19h4M13 16v3" stroke="#fff" stroke-width="1.3"/></svg><div style="font-size:5px;font-weight:700;color:var(--sky)">Lorem Ipsum</div><p class="txt">Lorem ipsum dolor sit amet, consectetur adipiscing elit</p></div>
    <div><svg width="26" height="26" viewBox="0 0 26 26"><circle cx="13" cy="13" r="12" fill="var(--navy)" stroke="#fff" stroke-width="1.5"/><circle cx="13" cy="13" r="5" fill="none" stroke="#fff" stroke-width="2.4" stroke-dasharray="2 1.4"/><circle cx="13" cy="13" r="1.8" fill="#fff"/></svg><div style="font-size:5px;font-weight:700;color:var(--navy)">Lorem Ipsum</div><p class="txt">Lorem ipsum dolor sit amet, consectetur adipiscing elit</p></div>
    <div><svg width="26" height="26" viewBox="0 0 26 26"><circle cx="13" cy="13" r="12" fill="#fff" stroke="#ccc" stroke-width="1.2"/><path d="M8 8l10 10M18 8l-10 10" stroke="var(--gray)" stroke-width="1.6"/></svg><div style="font-size:5px;font-weight:700;color:var(--gray)">Lorem Ipsum</div><p class="txt">Lorem ipsum dolor sit amet, consectetur adipiscing elit</p></div>
  </div>
  <div class="foot"><svg width="285" height="14"><path d="M0 4H45L50 9H285" stroke="var(--green)" stroke-width="1" fill="none"/><path d="M0 12.5H285" stroke="var(--navy)" stroke-width="1"/></svg><span class="mark"><i></i>KQA</span><span class="copy">Copyright © 2016 K Quadrant Advisory All rights reserved.</span><span class="pg">19</span></div>
</section>

<!-- 20 testimonials -->
<section class="slide" style="background:#55595c">
  <div class="photo" role="img" aria-label="Dark photo of doctors shaking hands" style="inset:0;background:linear-gradient(90deg,#4c5154 0%,#6b7174 50%,#464b4e 100%)"></div>
  <h2 class="title" style="left:0;right:0;text-align:center;color:#fff;font-size:10px">Testimonials</h2>
  <svg class="abs" style="left:130px;top:50px" width="25" height="25" viewBox="0 0 25 25"><circle cx="12.5" cy="12.5" r="11" fill="none" stroke="var(--green)" stroke-width="1.3"/><text x="12.5" y="18" fill="var(--green)" font-size="13" font-family="Open Sans, sans-serif" font-weight="700" text-anchor="middle">”</text></svg>
  <p class="abs txt" style="left:22px;right:22px;top:82px;text-align:center;color:#fff;font-size:4.8px">Lorem Ipsum is simply dummy text of the printing and typesetting industry. Lorem Ipsum has been the industry's standard dummy text ever since the 1500s, when an unknown printer took a galley of type and scrambled it to make a type specimen book.</p>
  <div class="abs" style="left:0;right:0;top:112px;text-align:center;font-size:5px;font-weight:700;font-style:italic;color:var(--green)">- John Doe -</div>
</section>

<!-- 21 thank you -->
<section class="slide" style="background:#2d3235">
  <div class="photo" role="img" aria-label="Dark photo of a smiling doctor" style="inset:0;background:linear-gradient(90deg,#24292c 0%,#3c4245 60%,#2a2f32 100%)"></div>
  <svg class="abs" width="285" height="161" viewBox="0 0 285 161">
    <polygon points="0,6 150,6 160,0 285,0 285,4 162,4 152,10 0,10" fill="var(--sky)"/>
    <polygon points="0,10 152,10 162,4 285,4 285,7 164,7 154,13 0,13" fill="var(--navy)"/>
    <polygon points="0,148 130,148 140,155 285,155 285,161 0,161" fill="var(--sky)"/>
    <polygon points="0,144 128,144 138,151 285,151 285,155 140,155 130,148 0,148" fill="var(--navy)"/>
  </svg>
  <div class="abs" style="left:10px;top:50px;font-size:9px;font-weight:700;color:#fff">THANK YOU FONT 24PT</div>
  <div class="abs" style="left:10px;top:68px;font-size:3.6px;color:#fff;line-height:1.35">
    <b>ADDRESS</b><br>Lorem ipsum<br><b>PHONE/FAX</b><br>Call: 555-300-6000<br>Lo-Call Number: 555-300-3000<br><b>EMAIL</b><br>dorrit@kquadrantadvisory.co<br><b>WEBSITE</b><br>www.kquadrantadvisory.co
  </div>
  <div class="abs" style="right:14px;top:52px"><span class="mark light" style="font-size:4px"><i></i>K QUADRANT ADVISORY</span></div>
  <p class="abs txt" style="left:165px;top:78px;width:108px;color:#e5e5e5;font-size:4.2px">Lorem Ipsum is simply dummy text of the printing and typesetting industry. Lorem Ipsum has been the industry's standard dummy text ever since the 1500s, when an unknown printer took a galley of type and scrambled it to make a type specimen. The industry's standard dummy text ever since the 1500s, when an unknown printer took a galley.</p>
</section>

</main>
</body>
</html>
```